Brightmill Data Works

Our company is about IT hardwares and IT solutions. IT hardware such as PC, RAMS, storage and servers. IT solutions such as project management, BA. We are also selling new technology too.

Target Market(s)

Consumer, Small to Medium Business, Corporate

Requirements
Must have
• The business card must have the following:
• Name:
• Title:
• Contact Number:
• Email address:
• Website:
• Color: Must match the logo color upgrade

```html
<!DOCTYPE html>
<html lang="en">
<head>
<meta charset="utf-8">
<title>Brightmill Data Works – Business Card</title>
<link rel="stylesheet" href="https://fonts.googleapis.com/css2?family=Lato:wght@400;700;900&display=swap">
<style>
  :root {
    --stage: #e9e9e9;
    --card-dark: #1e1e1e;
    --card-light: #ffffff;
    --amber: #e0962f;
    --ink: #3a3a3a;
    --ink-soft: #2b2b2b;
    --muted: #cfcfcf;
  }
  * { box-sizing: border-box; margin: 0; padding: 0; }
  html, body {
    width: 1200px; height: 912px; overflow: hidden;
    background: var(--stage);
    font-family: "Lato", Arial, sans-serif;
  }
  .stage { position: relative; width: 1200px; height: 912px; }
  .card {
    position: absolute; width: 600px; height: 343px; overflow: hidden;
    box-shadow: 0 8px 24px rgba(0,0,0,.18);
  }

  /* Back side */
  .card--back { left: 90px; top: 90px; background: var(--card-dark); }
  .card--back .brand {
    position: absolute; left: 0; right: 0; top: 128px;
    display: flex; align-items: center; justify-content: center; gap: 14px;
  }
  .brand__mark { width: 22px; height: 22px; background: var(--amber); }
  .brand__name {
    font-weight: 900; font-size: 30px; letter-spacing: 1px;
    text-transform: uppercase;
  }
  .card--back .brand__name { color: #ffffff; }
  .card--back .web {
    position: absolute; left: 0; right: 0; bottom: 48px; text-align: center;
    color: var(--muted); font-size: 14px; letter-spacing: .5px;
  }

  /* Front side */
  .card--front { left: 510px; top: 480px; background: var(--card-light); }
  .card--front .sweep { position: absolute; inset: 0; width: 600px; height: 343px; }
  .card--front .brand {
    position: absolute; right: 34px; top: 40px;
    display: flex; align-items: center; gap: 10px;
  }
  .card--front .brand__mark { width: 16px; height: 16px; }
  .card--front .brand__name { color: var(--ink); font-size: 22px; }
  .tab {
    position: absolute; left: 0; top: 150px; width: 0; height: 0;
    border-top: 14px solid transparent; border-bottom: 14px solid transparent;
    border-left: 16px solid var(--amber);
  }
  .person { position: absolute; left: 44px; top: 128px; }
  .person__name { color: var(--amber); font-weight: 700; font-size: 22px; }
  .person__title { color: var(--ink-soft); font-size: 14px; margin-top: 2px; }
  .address { position: absolute; left: 44px; top: 198px; color: var(--ink-soft); font-size: 14px; line-height: 19px; }
  .contacts { position: absolute; left: 44px; top: 248px; list-style: none; color: var(--ink-soft); font-size: 14px; }
  .contacts li { display: flex; align-items: center; gap: 10px; height: 19px; }
  .contacts svg { width: 13px; height: 13px; fill: var(--amber); flex: none; }
  .card--front .web {
    position: absolute; right: 26px; bottom: 22px;
    color: #ffffff; font-size: 14px; letter-spacing: .4px;
  }
</style>
</head>
<body>
<main class="stage">

  <section class="card card--back" aria-label="Business card, back">
    <div class="brand">
      <span class="brand__mark"></span>
      <span class="brand__name">Brightmill Data Works</span>
    </div>
    <p class="web">www.brightmilldata.com</p>
  </section>

  <section class="card card--front" aria-label="Business card, front">
    <svg class="sweep" viewBox="0 0 600 343" aria-hidden="true">
      <path fill="var(--amber)" d="M150,343 C360,318 500,228 588,118 L600,118 L600,142 C505,236 380,320 240,343 Z"/>
      <path fill="var(--card-dark)" d="M262,343 C405,322 525,246 600,158 L600,343 Z"/>
    </svg>

    <div class="brand">
      <span class="brand__mark"></span>
      <span class="brand__name">Brightmill Data Works</span>
    </div>

    <span class="tab"></span>

    <div class="person">
      <p class="person__name">Daniel Whitford</p>
      <p class="person__title">Manager</p>
    </div>

    <p class="address">418 Alder Creek Road<br>Austin, TX 78704</p>

    <ul class="contacts">
      <li>
        <svg viewBox="0 0 16 16" aria-label="Phone"><path d="M3.5 1 L6 1 L7 4.5 L5.3 5.8 C6.2 7.9 8.1 9.8 10.2 10.7 L11.5 9 L15 10 L15 12.5 C15 13.9 13.9 15 12.5 15 C6.7 15 1 9.3 1 3.5 C1 2.1 2.1 1 3.5 1 Z"/></svg>
        <span>555 014 2200</span>
      </li>
      <li>
        <svg viewBox="0 0 16 16" aria-label="Fax"><path d="M4 1 H12 V5 H4 Z M1 6 H15 V12 H13 V9 H3 V12 H1 Z M4 10 H12 V15 H4 Z"/></svg>
        <span>555 014 2201</span>
      </li>
      <li>
        <svg viewBox="0 0 16 16" aria-label="Email"><path d="M1 3 H15 V4 L8 9 L1 4 Z M1 5.5 L8 10.5 L15 5.5 V13 H1 Z"/></svg>
        <span>hello@brightmilldata.com</span>
      </li>
    </ul>

    <p class="web">www.brightmilldata.com</p>
  </section>

</main>
</body>
</html>
```